Closing our Shadle Office

I currently have a three location eye care practice located in Marrow Valley, Halden Ridge and Corven Marketfields. We are closing our Shadle location and hope to see these patients at our other practices.

I would like something that comes across as more friendly and appreciative... "Thank you for seeing us at our Corven Marketfield clinic. This location has now closed. We hope to continue to provide care for you at our Halden Ridge or Marrow Valley locations. -Dr Tobin Fairweather, Lotte and Mabel This will be on a postcard, so it needs to have space for address and stamp. Must have picture of the three of us on the front, and picture of both locations (wide view showing mural) on the back. (okay to include or leave out picture of me on back) Please include address with pictures: Marrow Valley Clinic- 48213 E Tamsworth Ave. Halden Ridge Clinic - 3086 S Penbrook Rd. Also need to include Phone number : 509-642-1038, www.brightlenscare.example, and hello@brightlenscare.example.

Target Market(s)

Current Shadle patients

Font styles to use
Serif
Sans Serif

Requirements
Must have
• Photo of myself and two staff.
• Photo of Halden Ridge and Valley office
• Photo with mural to left is my Airway office. Photo with mural to the right is Marrow Valley (Kettering Exit)
• Phone # 509-642-1038. www.brightlenscare.example
Nice to have
• Front of card with photo of myself, Lotte (darker hair on left) and Mabel (longer hair on right)
• Back of card with images of both other clinics and small photo of myself

```html
<!DOCTYPE html>
<html lang="en">
<head>
<meta charset="utf-8">
<title>Corven Marketfield Clinic Closing Postcard</title>
<link rel="stylesheet" href="https://fonts.googleapis.com/css2?family=Montserrat:ital,wght@0,500;0,600;0,700;1,600&family=Oswald:wght@600&display=swap">
<style>
  :root {
    --paper: #fbfbfc;
    --navy: #1f3566;
    --navy-deep: #1b2d5c;
    --panel-light: #1d5d9e;
    --brand-blue: #1e7fc8;
    --sky: #1ad4f0;
    --ink: #253766;
    --white: #ffffff;
  }
  * { margin: 0; padding: 0; box-sizing: border-box; }
  html, body {
    width: 1200px;
    height: 852px;
    overflow: hidden;
    background: var(--paper);
  }
  .postcard {
    position: relative;
    width: 1200px;
    height: 852px;
    background: var(--paper);
    font-family: "Montserrat", Arial, sans-serif;
    overflow: hidden;
  }
  .brand {
    position: absolute;
    left: 38px;
    top: 185px;
    width: 480px;
    display: flex;
    align-items: center;
    gap: 14px;
    white-space: nowrap;
  }
  .brand-dot {
    width: 40px;
    height: 40px;
    border-radius: 50%;
    background: var(--brand-blue);
    flex: none;
  }
  .brand-name {
    font-family: "Montserrat", Arial, sans-serif;
    font-weight: 700;
    font-size: 38px;
    letter-spacing: 0.5px;
    color: var(--navy);
    text-transform: uppercase;
    line-height: 1;
  }
  .message-panel {
    position: absolute;
    left: 16px;
    top: 315px;
    width: 521px;
    height: 360px;
    border-radius: 38px;
    background: radial-gradient(ellipse at 75% 60%, var(--panel-light) 0%, var(--navy) 60%, var(--navy-deep) 100%);
    color: var(--white);
    text-align: center;
    padding-top: 50px;
  }
  .message-text {
    font-weight: 500;
    font-size: 24px;
    line-height: 34.3px;
    letter-spacing: 2px;
    padding: 0 16px;
  }
  .message-sign {
    margin-top: 10px;
    font-weight: 600;
    font-style: italic;
    font-size: 19px;
    letter-spacing: 1px;
    color: var(--sky);
    white-space: nowrap;
  }
  .contacts {
    position: absolute;
    left: 58px;
    top: 688px;
  }
  .contacts-title {
    font-family: "Oswald", "Arial Narrow", sans-serif;
    font-weight: 600;
    font-size: 31px;
    letter-spacing: 2px;
    color: var(--brand-blue);
    line-height: 1.1;
  }
  .contacts-line {
    font-weight: 700;
    font-size: 23px;
    letter-spacing: 2.2px;
    color: var(--ink);
    line-height: 39px;
    white-space: nowrap;
  }
  .team-photo {
    position: absolute;
    left: 0;
    top: 0;
    width: 1200px;
    height: 852px;
  }
</style>
</head>
<body>
  <main class="postcard">
    <div class="brand">
      <span class="brand-dot"></span>
      <span class="brand-name">Brightlens Care</span>
    </div>

    <section class="message-panel">
      <p class="message-text">Thank you for seeing us at our Corven Marketfield clinic. This location has now closed. We hope to continue to provide care for you at our Halden Ridge or Marrow Valley locations.</p>
      <p class="message-sign">Dr Tobin Fairweather, Lotte and Mabel</p>
    </section>

    <section class="contacts">
      <h2 class="contacts-title">CONTACTS</h2>
      <p class="contacts-line">www.brightlenscare.example</p>
      <p class="contacts-line">hello@brightlenscare.example</p>
      <p class="contacts-line">509-642-1038</p>
    </section>

    <svg class="team-photo" viewBox="0 0 1200 852">
      <defs>
        <linearGradient id="team-tones" x1="0" y1="0" x2="0" y2="1">
          <stop offset="0" stop-color="#e4e1e3"/>
          <stop offset="0.4" stop-color="#c9b6a3"/>
          <stop offset="0.65" stop-color="#6e5545"/>
          <stop offset="1" stop-color="#1c1a1d"/>
        </linearGradient>
      </defs>
      <circle cx="1058" cy="426" r="520" fill="var(--brand-blue)"/>
      <circle cx="1064" cy="426" r="516" fill="var(--navy)"/>
      <circle cx="1068" cy="426" r="512" fill="url(#team-tones)" role="img" aria-label="Photo of Dr Tobin Fairweather with staff members Lotte and Mabel standing in front of a large eye chart wall"/>
    </svg>
  </main>
</body>
</html>
```